Morlavik APP redesign and color change

I am looking for a new design for my app. Please see the attached current design.

Currently, I have a functioning app but the colors and design are awful!
The logo is great but the rest of the app needs a refresh.
(Logo hi res not yet available but will upload soon.)
New colors or anything that is cutting edge.

Basically: It is a secure social media app within a school system where the teachers, students and parents can text, exchange photos, plan curriculum, etc.

I NEED ONLY landing page with a new look!
Looking for one distinct design for the landing page with new look.
The developer will apply this one design towards the rest of the pages/app screens.

Because part of the social media I need the feel and look of what is now the trend. Something that will attract and keep the client(s) interested. I am really leaving all the creative work to the designer and open to any suggestions.

Target Market(s)

Schools, community, teachers, students, colleges, sport teams

Industry/Entity Type

Non Profit

Font styles to use
Serif
Sans Serif

Colors

Designer to choose colors to be used in the design.

Requirements
Must have
• Sharp, trendy, millennial feel
Nice to have
• Up to designer
Should not have
• Up to designer

```html
<!DOCTYPE html>
<html lang="en">
<head>
<meta charset="utf-8">
<title>Morlavik — Landing Screen Options</title>
<link rel="stylesheet" href="https://fonts.googleapis.com/css2?family=Mulish:wght@400;600&family=Montserrat:wght@400;500;600;700&display=swap">
<style>
  :root {
    --board: #212731;
    --pink: #f47e9b;
    --violet: #6b6ee8;
    --teal: #3ab8c4;
    --teal-deep: #36b3bd;
    --white: #ffffff;
    --ink: #333a44;
    --line-light: rgba(255,255,255,0.45);
    --line-dark: #c9ccd1;
  }
  * { box-sizing: border-box; margin: 0; padding: 0; }
  html, body { width: 1024px; height: 1200px; overflow: hidden; background: var(--board); }
  body { position: relative; font-family: "Montserrat", sans-serif; color: var(--white); }

  .option-title {
    position: absolute; font-family: "Mulish", sans-serif; font-weight: 600;
    font-size: 36px; line-height: 1; transform: translateX(-50%); white-space: nowrap;
  }
  .option-title.pink { left: 264px; top: 113px; color: var(--pink); }
  .option-title.violet { left: 751px; top: 113px; color: var(--violet); }
  .option-title.teal { left: 508px; top: 641px; color: var(--teal); }

  .screen {
    position: absolute; width: 227px; height: 406px; overflow: hidden;
    box-shadow: 0 4px 10px rgba(0,0,0,0.35);
  }
  .photo { position: absolute; inset: 0; }

  .status-bar {
    position: absolute; top: 0; left: 0; right: 0; height: 12px;
    display: flex; align-items: center; justify-content: space-between;
    padding: 0 8px 0 10px; font-family: "Mulish", sans-serif; font-size: 7.5px; font-weight: 600;
    color: rgba(255,255,255,0.85); z-index: 2;
  }
  .status-bar .battery { display: inline-block; width: 15px; height: 6px; background: currentColor; border-radius: 1px; vertical-align: middle; margin-left: 2px; }
  .status-bar.dark { color: #111; }

  .brand { position: absolute; left: 0; right: 0; text-align: center; z-index: 2; }
  .brand-dot { display: block; margin: 0 auto; border: 2.5px solid var(--white); border-radius: 50%; }
  .brand-name { display: block; font-weight: 500; color: var(--white); }
  .brand.small { top: 62px; }
  .brand.small .brand-dot { width: 44px; height: 44px; }
  .brand.small .brand-name { font-size: 8px; letter-spacing: 4.5px; margin-top: 18px; padding-left: 4px; }
  .brand.splash { top: 158px; }
  .brand.splash .brand-dot { width: 66px; height: 66px; }
  .brand.splash .brand-name { font-size: 11px; letter-spacing: 6.5px; margin-top: 18px; padding-left: 6px; }
  .brand.hero { top: 92px; }
  .brand.hero .brand-dot { width: 86px; height: 86px; border-width: 3px; }
  .brand.hero .brand-name { font-size: 14px; letter-spacing: 9px; margin-top: 22px; padding-left: 9px; font-weight: 600; }
  .brand.on-white .brand-dot { border-color: var(--teal); }
  .brand.on-white .brand-name { color: var(--teal); }

  .field {
    position: absolute; left: 32px; right: 30px; height: 22px; z-index: 2;
    border-bottom: 1px solid var(--line-light);
    font-family: "Mulish", sans-serif; font-size: 9px; letter-spacing: 1.2px; text-align: center;
    line-height: 18px;
  }
  .field svg { position: absolute; left: 0; top: 2px; width: 12px; height: 14px; }
  .field.user { top: 180px; }
  .field.pass { top: 219px; }
  .light .field { color: var(--ink); border-bottom-color: var(--line-dark); }

  .actions { position: absolute; left: 33px; right: 30px; top: 292px; height: 24px; display: flex; align-items: center; z-index: 2; }
  .btn-login {
    width: 84px; height: 24px; border-radius: 12px; background: var(--white);
    font-size: 8.5px; font-weight: 700; letter-spacing: 1.2px; display: flex; align-items: center; justify-content: center;
    box-shadow: 0 2px 5px rgba(0,0,0,0.2);
  }
  .btn-signup { margin-left: 24px; font-size: 8.5px; font-weight: 700; letter-spacing: 1.6px; color: var(--white); }
  .opt1 .btn-login { color: var(--pink); }
  .opt2 .btn-login { color: var(--violet); }
  .opt3 .btn-login { background: var(--teal); color: var(--white); }
  .opt3 .btn-signup { color: var(--ink); font-weight: 600; }

  .tagline {
    position: absolute; left: 10px; right: 10px; top: 288px; z-index: 2; text-align: center;
    font-family: "Mulish", sans-serif; font-size: 8.6px; line-height: 12px; color: var(--white);
  }
  .btn-start {
    position: absolute; left: 14px; width: 201px; top: 344px; height: 31px; border-radius: 16px; z-index: 2;
    background: var(--white); color: var(--teal-deep); font-size: 9px; font-weight: 700; letter-spacing: 2.6px;
    display: flex; align-items: center; justify-content: center; gap: 10px;
  }
</style>
</head>
<body>

<h2 class="option-title pink">Option #1</h2>
<h2 class="option-title violet">Option #2</h2>
<h2 class="option-title teal">Option #3</h2>

<svg width="0" height="0" style="position:absolute">
  <defs>
    <symbol id="icon-user" viewBox="0 0 12 14"><circle cx="6" cy="4" r="3" fill="none" stroke="currentColor" stroke-width="0.9"/><path d="M0.8 13.2c0-3 2.3-5 5.2-5s5.2 2 5.2 5z" fill="none" stroke="currentColor" stroke-width="0.9"/></symbol>
    <symbol id="icon-lock" viewBox="0 0 12 14"><path d="M3 6V4a3 3 0 0 1 6 0v2" fill="none" stroke="currentColor" stroke-width="0.9"/><rect x="1" y="6" width="10" height="7.5" rx="1" fill="none" stroke="currentColor" stroke-width="0.9"/><path d="M3.5 10h5" stroke="currentColor" stroke-width="0.9" stroke-dasharray="1 1"/></symbol>
  </defs>
</svg>

<!-- Option 1 : splash -->
<section class="screen opt1" style="left:34px; top:171px;">
  <div class="photo" role="img" aria-label="Photo of students studying at a table with books, under a warm orange-to-pink tint" style="background:linear-gradient(180deg,#e2ae83 0%,#e59a8a 45%,#ec7f9c 80%,#f27ba0 100%);"></div>
  <div class="status-bar"><span>●●●○○</span><span>4:21 PM</span><span>100% <i class="battery"></i></span></div>
  <div class="brand splash"><span class="brand-dot"></span><span class="brand-name">MORLAVIK</span></div>
</section>

<!-- Option 1 : login -->
<section class="screen opt1" style="left:277px; top:171px;">
  <div class="photo" role="img" aria-label="Photo of students studying at a wooden table, darkened for contrast" style="background:radial-gradient(ellipse at 80% 20%,#6e5a34 0%,transparent 45%),linear-gradient(180deg,#5a4a3e 0%,#4a3a30 50%,#3a2b24 100%);"></div>
  <div class="status-bar"><span>●●●○○</span><span>4:21 PM</span><span>100% <i class="battery"></i></span></div>
  <div class="brand small"><span class="brand-dot"></span><span class="brand-name">MORLAVIK</span></div>
  <div class="field user"><svg><use href="#icon-user"/></svg>Username</div>
  <div class="field pass"><svg><use href="#icon-lock"/></svg>Password</div>
  <div class="actions"><span class="btn-login">LOGIN</span><span class="btn-signup">SIGN UP</span></div>
</section>

<!-- Option 2 : splash -->
<section class="screen opt2" style="left:519px; top:171px; background:linear-gradient(155deg,#3d4f8e 0%,#5450c8 50%,#6c7de8 100%);">
  <div class="status-bar"><span>●●●○○</span><span>4:21 PM</span><span>100% <i class="battery"></i></span></div>
  <div class="brand splash"><span class="brand-dot"></span><span class="brand-name">MORLAVIK</span></div>
</section>

<!-- Option 2 : login -->
<section class="screen opt2" style="left:762px; top:171px; background:linear-gradient(155deg,#3d4f8e 0%,#5450c8 50%,#6c7de8 100%);">
  <div class="status-bar"><span>●●●○○</span><span>4:21 PM</span><span>100% <i class="battery"></i></span></div>
  <div class="brand small"><span class="brand-dot"></span><span class="brand-name">MORLAVIK</span></div>
  <div class="field user"><svg><use href="#icon-user"/></svg>Username</div>
  <div class="field pass"><svg><use href="#icon-lock"/></svg>Password</div>
  <div class="actions"><span class="btn-login">LOGIN</span><span class="btn-signup">SIGN UP</span></div>
</section>

<!-- Option 3 : welcome -->
<section class="screen opt3" style="left:277px; top:700px;">
  <div class="photo" role="img" aria-label="Photo of students studying together, under a teal tint" style="background:linear-gradient(180deg,#45b8bd 0%,#4cc0c4 50%,#45bcc2 100%);"></div>
  <div class="status-bar"><span>●●●○○</span><span>4:21 PM</span><span>100% <i class="battery"></i></span></div>
  <div class="brand hero"><span class="brand-dot"></span><span class="brand-name">MORLAVIK</span></div>
  <p class="tagline">Communicate with other students, teachers,<br>and parents through secure and safe platform</p>
  <div class="btn-start">GET STARTED NOW
    <svg width="16" height="10" viewBox="0 0 16 10"><path d="M1 5h13M10 1l4 4-4 4" fill="none" stroke="currentColor" stroke-width="1.2"/></svg>
  </div>
</section>

<!-- Option 3 : login -->
<section class="screen opt3 light" style="left:519px; top:700px; background:var(--white);">
  <div class="status-bar dark"><span>●●●○○</span><span>4:21 PM</span><span>100% <i class="battery"></i></span></div>
  <div class="brand small on-white"><span class="brand-dot"></span><span class="brand-name">MORLAVIK</span></div>
  <div class="field user"><svg style="color:var(--teal)"><use href="#icon-user"/></svg>Username</div>
  <div class="field pass"><svg style="color:var(--teal)"><use href="#icon-lock"/></svg>Password</div>
  <div class="actions"><span class="btn-login">LOGIN</span><span class="btn-signup">SIGN UP</span></div>
</section>

</body>
</html>
```